Travel Agency Website - Simple General

Need a 7 page simple design that is pretty repetitive. Need to be able to load quickly that is SEO optimized. Trying to give ideas on what they can do, be personal as we are local, but at the same time come across as professional and get information easily with little burden.

- Landing Page
- Brimwell Vacations Page
- Family Trips
- Road Trips from Texas
- Other Destinations
- About Us Page
- Contact Us Page

Target Market(s)

Families

Coding

Coded - Design and coding required

Number of Pages Required

5+ page

Colors

Designer to choose colors to be used in the design.

Requirements
Must have
• Like it to flow easily with our logo. Use that for colors, etc.

```html
<!DOCTYPE html>
<html lang="en">
<head>
<meta charset="utf-8">
<title>Roamwell Travel Co. – Explore the World</title>
<meta name="description" content="Personalized family vacations, road trips and worldwide escapes by Roamwell Travel Co.">
<link rel="stylesheet" href="https://fonts.googleapis.com/css2?family=Outfit:wght@300;400;500;600;700;800&family=League+Spartan:wght@700;800&family=Yellowtail&display=swap">
<style>
:root{
  --teal:#1c5f6b;
  --teal-dark:#174f59;
  --gold:#c39a55;
  --ink:#1d1b1a;
  --muted:#6d6a66;
  --cream:#fdf9f5;
  --sand:#f5efe6;
  --white:#ffffff;
}
*{box-sizing:border-box;margin:0;padding:0}
html,body{width:1200px;height:2541px;overflow:hidden}
body{position:relative;background:var(--cream);font-family:"Outfit",sans-serif;color:var(--ink)}
.abs{position:absolute}
a{color:inherit;text-decoration:none}
.btn{position:absolute;display:flex;align-items:center;justify-content:center;background:var(--teal);color:var(--white);border-radius:30px;font-weight:500;font-size:15px}
.script{font-family:"Yellowtail",cursive;color:var(--gold)}
.photo{position:absolute;overflow:hidden}

/* header */
.brand{left:95px;top:50px;display:flex;align-items:center;gap:10px;font-size:22px;font-weight:600;color:var(--teal)}
.brand-dot{width:16px;height:16px;border-radius:50%;background:var(--teal)}
.nav{left:389px;top:64px;display:flex;gap:52px;font-size:16px}
.nav .active{color:var(--teal);font-weight:500}
.social{top:66px;width:17px;height:17px;border-radius:50%;border:2px solid var(--teal)}

/* hero */
.tagline{left:93px;top:198px;font-size:27px}
.hero-title{left:90px;top:246px;font-family:"League Spartan",sans-serif;font-weight:800;font-size:88px;line-height:80px;letter-spacing:1px;color:var(--ink)}
.hero-copy{left:88px;top:426px;width:430px;font-size:13px;line-height:24px;color:#2e2c2a}
.video-badge{width:78px;height:78px;border-radius:50%;background:var(--white);box-shadow:0 4px 14px rgba(0,0,0,.08);display:flex;align-items:center;justify-content:center}
.play{width:22px;height:22px;border-radius:50%;background:var(--gold);display:flex;align-items:center;justify-content:center}
.hero-photo{left:733px;top:188px;width:385px;height:383px;border-radius:50% 50% 0 50%;background:linear-gradient(135deg,#6d7d43 0%,#b48a62 45%,#5b4636 100%)}

/* stats */
.stat-num{left:237px;top:672px;font-size:27px;font-weight:600}
.stat-label{left:237px;top:712px;font-size:15px;color:var(--muted)}
.customers{left:440px;top:666px;width:262px;height:76px;border-radius:40px;background:var(--white);box-shadow:0 8px 24px rgba(0,0,0,.07)}
.customers h4{position:absolute;left:23px;top:12px;font-size:13.5px;font-weight:600}
.customers p{position:absolute;left:23px;top:34px;width:135px;font-size:11px;line-height:17px;color:var(--muted)}
.story h3{font-size:19px;font-weight:600}
.story p{margin-top:4px;width:240px;font-size:12px;line-height:20px;font-weight:500;color:var(--muted)}
.story-arrow{left:1033px;top:664px;width:65px;height:81px;border-radius:40px 40px 40px 0;background:var(--gold);display:flex;align-items:center;justify-content:center}

/* categories */
.eyebrow{left:0;width:1220px;text-align:center;font-size:24px}
.section-title{left:0;width:1220px;text-align:center;top:877px;font-size:44px;font-weight:400;letter-spacing:-.5px}
.section-title b{font-weight:700}
.intro{top:957px;width:452px;font-size:15px;line-height:26px;color:#2e2c2a;text-align:justify}
.card{position:absolute;top:1075px;width:262px}
.card-img{height:257px;border-radius:16px;position:relative}
.heart{position:absolute;right:16px;top:17px;width:24px;height:24px;border-radius:50%;border:1.5px solid var(--white);display:flex;align-items:center;justify-content:center}
.dots{position:absolute;bottom:22px;left:0;right:0;display:flex;justify-content:center;gap:5px}
.dots i{width:5px;height:5px;border-radius:50%;background:rgba(255,255,255,.6)}
.dots i.on{background:var(--white)}
.card h3{margin:20px 0 0 4px;font-size:16.5px;font-weight:500}
.card p{margin:6px 0 0 4px;font-size:12.5px;color:var(--muted)}
.rating{margin:9px 0 0 4px;display:flex;align-items:center;gap:8px;font-size:10px;color:#444}
.rating span.pill{background:#fbe3d3;border-radius:10px;padding:2px 6px;font-weight:600;display:flex;align-items:center;gap:3px}

/* adventures */
.adventure-band{left:0;top:1470px;width:1200px;height:620px;background:linear-gradient(180deg,var(--white) 0%,var(--sand) 100%)}
.adv-title{left:120px;top:1512px;font-size:50px;line-height:62px;font-weight:400;letter-spacing:-.5px}
.adv-title b{font-weight:700}
.adv-copy{font-size:17px;line-height:30px;color:#2e2c2a}
.group-photo{left:281px;top:1660px;width:818px;height:257px;border-radius:120px 130px 130px 0;background:linear-gradient(100deg,#d9b27a 0%,#e9c79a 35%,#c88e6a 65%,#a97a63 100%)}

/* footer */
.footer{left:0;top:2090px;width:1200px;height:451px;background:var(--teal);color:var(--white)}
.footer h4{position:absolute;top:84px;font-size:20.5px;font-weight:600;letter-spacing:.2px}
.footer ul{position:absolute;list-style:none;font-size:15px;line-height:30px}
.contact-item{display:flex;align-items:center;gap:10px}
.contact-item svg{width:16px}
.footer .indent{padding-left:26px}
.follow li{display:flex;align-items:center;gap:12px;margin-bottom:14px}
.follow i{width:24px;height:24px;border-radius:50%;border:1.5px solid var(--white);display:block}
.footer-brand{left:780px;top:130px;width:240px;display:flex;align-items:center;gap:12px;font-size:32px;font-weight:600}
.footer-brand span.mark{width:22px;height:22px;border-radius:50%;background:var(--white)}
.footer-rule{left:112px;top:356px;width:978px;height:1px;background:rgba(255,255,255,.35)}
.copyright{left:0;top:391px;width:1200px;text-align:center;font-size:15px}
</style>
</head>
<body>

<header>
  <a class="abs brand" href="#"><span class="brand-dot"></span>Roamwell Travel Co.</a>
  <nav class="abs nav">
    <a class="active" href="#">Home</a>
    <a href="#">About Us</a>
    <a href="#">Vacations</a>
    <a href="#">Contact Us</a>
  </nav>
  <a class="abs social" style="left:857px" href="#" aria-label="Socialbook"></a>
  <a class="abs social" style="left:893px" href="#" aria-label="Snapgram"></a>
  <a class="btn" style="left:949px;top:53px;width:149px;height:43px" href="#">Start A Journey</a>
</header>

<main>
  <section class="hero">
    <p class="abs script tagline">Making Memories, One Adventure at a Time</p>
    <h1 class="abs hero-title">EXPLORE<br>WORLD</h1>
    <div class="abs video-badge" style="left:526px;top:256px">
      <span class="play"><svg width="8" height="9" viewBox="0 0 8 9"><path d="M0 0l8 4.5L0 9z" fill="#fff"/></svg></span>
    </div>
    <p class="abs hero-copy">We create personalized vacations designed around your family, your dreams, and your budget — from magical Brimwell adventures to unforgettable road trips and worldwide escapes.</p>
    <a class="btn" style="left:93px;top:514px;width:184px;height:51px" href="#">Start Planning Today</a>
    <div class="photo hero-photo" role="img" aria-label="Smiling woman in sunglasses sitting in an open jeep in a green field"></div>
  </section>

  <section class="stats">
    <div class="photo" style="left:95px;top:664px;width:80px;height:80px;border-radius:50%;background:linear-gradient(180deg,#6aa0d0,#c07a4a)" role="img" aria-label="Desert canyon landscape"></div>
    <div class="photo" style="left:158px;top:664px;width:80px;height:80px;border-radius:50%;border:3px solid var(--cream);background:linear-gradient(180deg,#8fb6d9,#7a9a5c)" role="img" aria-label="City skyline above a green park"></div>
    <p class="abs stat-num">10,000+</p>
    <p class="abs stat-label">Travel Places</p>
    <div class="abs customers">
      <h4>Happy Customers</h4>
      <p>Sint occaecat cupidatat non proident, sunt</p>
      <div class="photo" style="left:182px;top:4px;width:80px;height:70px;border-radius:50%;border:6px solid var(--teal);background:linear-gradient(180deg,#9cc6e0,#d9b48f)" role="img" aria-label="Happy traveller portrait"></div>
    </div>
    <div class="abs story" style="left:767px;top:673px">
      <h3>Our Story</h3>
      <p>Duis aute irure dolor in reprehenderit in voluptate velit esse</p>
    </div>
    <a class="abs story-arrow" href="#" aria-label="Read our story">
      <svg width="36" height="14" viewBox="0 0 36 14" fill="none" stroke="#fff" stroke-width="2"><path d="M0 7h34M28 1l6 6-6 6"/></svg>
    </a>
  </section>

  <section class="categories">
    <p class="abs script eyebrow" style="top:840px">Wander Your Way</p>
    <h2 class="abs section-title">FEATURED <b>TRAVEL</b> CATEGORIES</h2>
    <p class="abs intro" style="left:120px">Lorem ipsum dolor sit amet, consectetur adipiscing elit, sed do eiusmod tempor incididunt ut labore et dolore magna aliqua. Ut ullamco laboris nisi ut aliquip ex ea commodo consequat.</p>
    <p class="abs intro" style="left:652px">Lorem ipsum dolor sit amet, consectetur adipiscing elit, sed do eiusmod tempor incididunt ut labore et dolore magna aliqua. Ut ullamco laboris nisi ut aliquip ex ea commodo consequat.</p>

    <article class="card" style="left:60px">
      <div class="card-img" role="img" aria-label="Fairytale castle under a blue sky" style="background:linear-gradient(180deg,#2f7fd0 0%,#7fb2e0 55%,#6e6a5e 100%)">
        <span class="heart"><svg width="11" height="10" viewBox="0 0 11 10" fill="none" stroke="#fff" stroke-width="1.3"><path d="M5.5 9L1.3 5A2.4 2.4 0 015.5 1.8 2.4 2.4 0 019.7 5z"/></svg></span>
        <span class="dots"><i></i><i class="on"></i><i></i><i></i><i></i></span>
      </div>
      <h3>Brimwell Vacations</h3><p>Land &amp; Sea Adventures</p>
      <div class="rating"><span class="pill"><svg width="9" height="9" viewBox="0 0 10 10"><path d="M5 0l1.5 3.3 3.5.4-2.6 2.4.7 3.5L5 7.8 1.9 9.6l.7-3.5L0 3.7l3.5-.4z" fill="#e8642c"/></svg>4.8</span>(21.k Review)</div>
    </article>

    <article class="card" style="left:340px">
      <div class="card-img" role="img" aria-label="Family cheering on a car by the sea" style="background:linear-gradient(180deg,#4aa3d8 0%,#8cc7e6 50%,#3a7fb0 100%)">
        <span class="heart"><svg width="11" height="10" viewBox="0 0 11 10" fill="none" stroke="#fff" stroke-width="1.3"><path d="M5.5 9L1.3 5A2.4 2.4 0 015.5 1.8 2.4 2.4 0 019.7 5z"/></svg></span>
        <span class="dots"><i></i><i class="on"></i><i></i><i></i><i></i></span>
      </div>
      <h3>Family Trips</h3><p>Made for Meaningful Memories</p>
      <div class="rating"><span class="pill"><svg width="9" height="9" viewBox="0 0 10 10"><path d="M5 0l1.5 3.3 3.5.4-2.6 2.4.7 3.5L5 7.8 1.9 9.6l.7-3.5L0 3.7l3.5-.4z" fill="#e8642c"/></svg>4.8</span>(21.k Review)</div>
    </article>

    <article class="card" style="left:619px">
      <div class="card-img" role="img" aria-label="Open desert highway toward red rock buttes" style="background:linear-gradient(180deg,#2a6fc4 0%,#8ab7de 40%,#b5743f 62%,#3a3734 100%)">
        <span class="heart"><svg width="11" height="10" viewBox="0 0 11 10" fill="none" stroke="#fff" stroke-width="1.3"><path d="M5.5 9L1.3 5A2.4 2.4 0 015.5 1.8 2.4 2.4 0 019.7 5z"/></svg></span>
        <span class="dots"><i></i><i class="on"></i><i></i><i></i><i></i></span>
      </div>
      <h3>Texas Road Trips</h3><p>Adventure Close to Home</p>
      <div class="rating"><span class="pill"><svg width="9" height="9" viewBox="0 0 10 10"><path d="M5 0l1.5 3.3 3.5.4-2.6 2.4.7 3.5L5 7.8 1.9 9.6l.7-3.5L0 3.7l3.5-.4z" fill="#e8642c"/></svg>4.8</span>(21.k Review)</div>
    </article>

    <article class="card" style="left:899px">
      <div class="card-img" role="img" aria-label="Sunset over waves on a sandy beach" style="background:linear-gradient(180deg,#f0b48a 0%,#f7d2a4 30%,#6fb0bf 55%,#d9c2a6 100%)">
        <span class="heart"><svg width="11" height="10" viewBox="0 0 11 10" fill="none" stroke="#fff" stroke-width="1.3"><path d="M5.5 9L1.3 5A2.4 2.4 0 015.5 1.8 2.4 2.4 0 019.7 5z"/></svg></span>
        <span class="dots"><i></i><i class="on"></i><i></i><i></i><i></i></span>
      </div>
      <h3>Other Destinations</h3><p>The World is Waiting</p>
      <div class="rating"><span class="pill"><svg width="9" height="9" viewBox="0 0 10 10"><path d="M5 0l1.5 3.3 3.5.4-2.6 2.4.7 3.5L5 7.8 1.9 9.6l.7-3.5L0 3.7l3.5-.4z" fill="#e8642c"/></svg>4.8</span>(21.k Review)</div>
    </article>
  </section>

  <section class="adventures">
    <div class="abs adventure-band"></div>
    <h2 class="abs adv-title">ADVENTURES <b>CAN FILL</b><br><b>YOUR SOUL</b></h2>
    <a class="btn" style="left:888px;top:1517px;width:200px;height:51px" href="#">Learn More About Us</a>
    <p class="abs adv-copy" style="left:482px;top:1584px;width:590px">Travel is more than just visiting places—it’s about creating unforgettable memories, experiencing new cultures, and embracing adventure.</p>
    <div class="abs video-badge" style="left:121px;top:1718px;width:106px;height:106px">
      <span class="play"><svg width="8" height="9" viewBox="0 0 8 9"><path d="M0 0l8 4.5L0 9z" fill="#fff"/></svg></span>
    </div>
    <svg class="abs" style="left:166px;top:1866px" width="20" height="126" viewBox="0 0 20 126" fill="none" stroke="#1d1b1a" stroke-width="2"><path d="M10 0v122M1 112l9 10 9-10"/></svg>
    <div class="photo group-photo" role="img" aria-label="Group of laughing friends on a sunny beach"></div>
    <p class="abs adv-copy" style="left:281px;top:1937px;width:822px">We’re a family-owned travel company passionate about helping others experience the joy of travel. From magical theme parks to scenic escapes, we love creating trips that bring people together.</p>
  </section>
</main>

<footer class="abs footer">
  <h4 style="left:110px">QUICK LINKS</h4>
  <ul style="left:111px;top:125px">
    <li><a href="#">Home</a></li><li><a href="#">About Us</a></li><li><a href="#">Vacations</a></li><li><a href="#">Contact Us</a></li>
  </ul>

  <h4 style="left:295px">CONTACT US</h4>
  <ul style="left:296px;top:125px">
    <li class="contact-item"><svg viewBox="0 0 16 16" height="16"><path d="M8 1a5 5 0 015 5c0 4-5 9-5 9S3 10 3 6a5 5 0 015-5zm0 3a2 2 0 100 4 2 2 0 000-4z" fill="#fff"/></svg>ADDRESS</li>
    <li class="indent">Roamwell Travel Co., US</li>
    <li class="contact-item"><svg viewBox="0 0 16 16" height="16"><path d="M3 1.5l3 .5 1 3-2 1.5c1 2 2.5 3.5 4.5 4.5L11 9l3 1 .5 3-2 1.5C7 14 2 9 1.5 3.5z" fill="#fff"/></svg>PHONE NUMBER</li>
    <li class="indent">+1 555 014 2270</li>
    <li class="contact-item"><svg viewBox="0 0 16 16" height="16"><rect x="1" y="3" width="14" height="10" rx="1" fill="#fff"/><path d="M1.5 4L8 9l6.5-5" stroke="#1c5f6b" stroke-width="1.3" fill="none"/></svg>Email Us</li>
    <li class="indent">hello@roamwelltravel.com</li>
  </ul>

  <h4 style="left:580px">FOLLOW US</h4>
  <ul class="follow" style="left:577px;top:132px;line-height:24px">
    <li><i></i><a href="#">Socialbook</a></li>
    <li><i></i><a href="#">Snapgram</a></li>
  </ul>

  <div class="abs footer-brand"><span class="mark"></span>Roamwell</div>
  <div class="abs footer-rule"></div>
  <p class="abs copyright">Copyrights@2026.Roamwell Travel Co.All Rights Reserved</p>
</footer>

</body>
</html>
```